business card deign

Logo needs the following on it.
1. attached logo
2. Tagline - "From icy drinks to lively parties...we bring it all along!"
3. Name- Dalton Pikes, Founder and CPO
4. Address - 412 E. Carver Avenue, Ste 2207, Tampa, FL. 33917
5. Phone - 555.318.4726

```html
<!DOCTYPE html>
<html lang="en">
<head>
<meta charset="utf-8">
<title>Bounder business card</title>
<link href="https://fonts.googleapis.com/css2?family=Montserrat:wght@400;700&display=swap" rel="stylesheet">
<style>
  :root {
    --backdrop: #8a6f4e;
    --card-dark: #050505;
    --card-light: #ffffff;
    --ink-light: #ffffff;
    --ink-dark: #111111;
    --rule: #555555;
  }
  * { box-sizing: border-box; margin: 0; padding: 0; }
  html, body { width: 1200px; height: 931px; overflow: hidden; }
  body {
    background: var(--backdrop);
    font-family: "Montserrat", sans-serif;
    position: relative;
  }
  .card {
    position: absolute;
    width: 640px;
    height: 366px;
    border-radius: 22px;
    box-shadow: 0 14px 30px rgba(0,0,0,0.35);
    overflow: hidden;
  }
  .card-front {
    left: 60px; top: 70px;
    background: var(--card-dark);
    color: var(--ink-light);
    display: flex; flex-direction: column; align-items: center; justify-content: center;
  }
  .brand {
    display: flex; align-items: center; gap: 14px;
    font-weight: 700; letter-spacing: 0.38em;
    white-space: nowrap;
  }
  .brand-dot { width: 16px; height: 16px; border-radius: 50%; background: currentColor; flex: none; }
  .card-front .brand { font-size: 44px; margin-top: 40px; }
  .tagline {
    margin-top: 48px;
    font-size: 15px; font-weight: 400; letter-spacing: 0.03em;
  }
  .card-back {
    left: 500px; top: 495px;
    background: var(--card-light);
    color: var(--ink-dark);
    display: flex; align-items: center;
  }
  .back-brand {
    width: 330px; display: flex; justify-content: center;
  }
  .back-brand .brand { font-size: 30px; margin-top: 60px; gap: 12px; }
  .back-brand .brand-dot { width: 13px; height: 13px; }
  .divider {
    width: 1px; height: 250px; background: var(--rule);
  }
  .contact { padding-left: 34px; font-size: 14px; line-height: 1.35; }
  .person-name { font-size: 26px; font-weight: 700; }
  .person-title { font-size: 15px; margin-bottom: 14px; }
  .contact-row { display: flex; align-items: center; gap: 12px; margin-bottom: 4px; }
  .contact-row svg { width: 16px; height: 16px; flex: none; }
  .address { margin-top: 12px; font-size: 15px; }
</style>
</head>
<body>
  <section class="card card-front">
    <div class="brand"><span class="brand-dot"></span>BOUNDER</div>
    <p class="tagline">From icy drinks to lively parties...we bring it all along!</p>
  </section>

  <section class="card card-back">
    <div class="back-brand">
      <div class="brand"><span class="brand-dot"></span>BOUNDER</div>
    </div>
    <div class="divider"></div>
    <div class="contact">
      <h1 class="person-name">Dalton Pikes</h1>
      <p class="person-title">Founder and CPO</p>
      <div class="contact-row">
        <svg viewBox="0 0 16 16" aria-hidden="true"><path d="M3 1.5l3 3-1.6 1.8a9 9 0 0 0 5.3 5.3L11.5 10l3 3-2 2C6.5 14.5 1.5 9.5 1 3.5z" fill="currentColor"/></svg>
        <span>555.318.4726</span>
      </div>
      <div class="contact-row">
        <svg viewBox="0 0 16 16" aria-hidden="true"><rect x="1" y="3" width="14" height="10" fill="none" stroke="currentColor" stroke-width="1.6"/><path d="M1 3l7 6 7-6" fill="none" stroke="currentColor" stroke-width="1.6"/></svg>
        <span>info@email.com</span>
      </div>
      <div class="contact-row">
        <svg viewBox="0 0 16 16" aria-hidden="true"><g fill="none" stroke="currentColor" stroke-width="1.4"><circle cx="8" cy="8" r="6.5"/><ellipse cx="8" cy="8" rx="3" ry="6.5"/><path d="M1.5 8h13M2.5 4.8h11M2.5 11.2h11"/></g></svg>
        <span>www.websitename.com</span>
      </div>
      <p class="address">412 E. Carver Avenue, Ste 2207,<br>Tampa, FL. 33917</p>
    </div>
  </section>
</body>
</html>
```